Tidewell-Network Theme For Forums!

We are looking for a theme for our forums. The forums are ran off Invision Power Boards. We have a basic theme on there now but we want more our own feel. If possible have some longboarding accept incorporated in the theme. We want the theme to have some red in it to match our logo. Tidewell-network.com

Target Market(s)

Skatingboarding & Longboarding

Coding

Coded - Design and coding required

Number of Pages Required

1 page

Colors
f04a50

```html
<!DOCTYPE html>
<html lang="en">
<head>
<meta charset="utf-8">
<title>Tidewell-Network Forums</title>
<link href="https://fonts.googleapis.com/css2?family=Lato:ital,wght@0,400;0,700;1,400&display=swap" rel="stylesheet">
<style>
:root{
  --red:#ec2f3b;
  --red-text:#e11f2c;
  --dark:#3d3d3d;
  --panel-head:#454545;
  --ink:#1b1b1b;
  --muted:#777;
  --line:#dcdcdc;
  --row-alt:#f6f6f6;
  --subhead:#f2f2f2;
  --footer:#2f2f2f;
}
*{box-sizing:border-box;margin:0;padding:0}
html,body{width:1052px;height:1200px;overflow:hidden}
body{font-family:'Lato',sans-serif;font-size:12px;color:var(--ink);background:#fff;position:relative}
.site-header{height:84px;position:relative}
.brand{position:absolute;left:70px;top:31px;display:flex;align-items:center;gap:8px}
.brand-mark{width:16px;height:16px;background:var(--red)}
.brand-name{font-size:25px;font-weight:700;color:#1b1b1b;letter-spacing:.5px}
.user-box{position:absolute;left:760px;top:19px;display:flex;gap:20px}
.avatar{width:45px;height:45px;border-radius:50%;background:linear-gradient(#d9c2b0,#b79885)}
.user-meta{padding-top:9px;font-size:11px}
.user-line{display:flex;gap:14px;align-items:center}
.user-links{color:var(--red-text);font-size:10px;margin-top:5px}
.main-nav{height:42px;background:var(--red);border-bottom:3px solid #111;position:relative}
.nav-list{position:absolute;left:70px;top:9px;display:flex;list-style:none}
.nav-list li{color:#fff;font-weight:700;font-size:12.5px;padding:0 19px;height:33px;line-height:33px}
.nav-list li.active{background:#111;border-radius:8px 8px 0 0;padding:0 23px}
.search{position:absolute;left:710px;top:9px;width:272px;height:22px;display:flex;background:#fff}
.search-scope{width:66px;background:#e4e4e4;font-size:11px;padding:4px 7px;display:flex;justify-content:space-between}
.search-input{flex:1;font-size:10.5px;padding:5px 7px;display:flex;justify-content:space-between}
.welcome{position:absolute;left:31px;top:139px;width:951px;height:38px;border:1px solid var(--line);display:flex;justify-content:space-between;align-items:center;padding:0 14px 0 11px;font-size:11.5px;color:#555}
.welcome b{color:#111}
.welcome .hl{color:var(--red-text);font-weight:700}
.new-content{color:var(--red-text)}
.panel{position:absolute;border:1px solid var(--line);background:#fff}
.panel-head{height:35px;background:var(--panel-head);color:#fff;font-size:15px;padding:0 15px;display:flex;align-items:center;justify-content:space-between}
.collapse{width:11px;height:11px;background:#eee;border-radius:2px;position:relative}
.collapse::after{content:"";position:absolute;left:2px;right:2px;top:5px;height:1.5px;background:#444}
.topic-grid{display:grid;grid-template-columns:57px 329px 79px 73px 135px 1fr}
.col-head{height:33px;background:var(--subhead);border-bottom:1px solid var(--line);color:var(--red-text);font-size:11.5px;align-items:center}
.col-head span{padding-left:12px}
.col-head span:first-child{padding:0}
.topic-row{height:56px;align-items:center}
.topic-row:nth-of-type(odd){background:var(--row-alt)}
.topic-row>div{height:100%;display:flex;flex-direction:column;justify-content:center;padding-left:12px}
.topic-row>.ico{padding:0;align-items:center;border-right:1px solid var(--line)}
.topic-row>.started,.topic-row>.stats,.topic-row>.last{border-right:1px solid var(--line)}
.title{font-size:12.5px}
.sub{font-style:italic;color:var(--muted);font-size:10.5px;margin-top:4px}
.by{font-style:italic;color:var(--red-text);font-size:10.5px;margin-top:4px}
.check{width:11px;height:11px;border:1px solid #ccc;margin-left:1px}
.stat-label{height:33px;background:var(--subhead);border-top:1px solid var(--line);border-bottom:1px solid var(--line);font-weight:700;font-size:11.5px;padding:0 16px;display:flex;align-items:center;color:#333}
.stat-item{height:56px;display:flex;align-items:center}
.stat-item .ico{width:57px;height:100%;display:flex;align-items:center;justify-content:center;border-right:1px solid var(--line)}
.stat-item .body{padding-left:12px}
.red{color:var(--red-text)}
.side-item{display:flex;gap:10px;padding:14px 14px 0;height:65px;border-bottom:1px solid #eee}
.side-item:last-of-type{border-bottom:none}
.thumb{width:47px;height:46px;background:linear-gradient(#c9ccd1,#8a8f96)}
.side-text{font-size:11.5px;line-height:1.3}
.side-meta{font-style:italic;color:var(--red-text);font-size:10.5px;margin-top:6px}
.view-all{height:25px;border-top:1px solid var(--line);background:var(--subhead);text-align:right;padding:6px 14px;font-size:10px}
.list-item{height:54px;padding:0 14px;display:flex;flex-direction:column;justify-content:center;border-bottom:1px solid var(--line);font-size:11.5px}
.list-item:last-child{border-bottom:none}
.list-item .meta{font-style:italic;color:var(--red-text);font-size:10.5px;margin-top:7px}
.list-item .sub{margin-top:6px}
.tabs{height:38px;display:flex;align-items:center;padding:0 8px;gap:18px;border-bottom:1px solid var(--line);font-size:11.5px}
.tab-on{background:var(--red);color:#fff;padding:4px 10px}
.online{position:absolute;left:753px;top:982px;width:229px;height:128px;border:1px solid var(--line);padding:20px 15px}
.online-top{display:flex;align-items:center;gap:18px;color:var(--red-text);font-size:12px;line-height:1.4;padding-left:8px}
.online-info{margin-top:19px;font-size:10.5px;color:#444;line-height:1.65}
.site-footer{position:absolute;left:0;top:1140px;width:1052px;height:60px;background:var(--footer);color:#bbb;font-size:10.5px;text-align:center;line-height:60px}
</style>
</head>
<body>
<svg width="0" height="0" style="position:absolute">
  <symbol id="board" viewBox="0 0 30 30">
    <g transform="rotate(-45 15 15)">
      <rect x="1" y="9" width="28" height="12" rx="6" fill="var(--red)"/>
      <circle cx="8" cy="6.5" r="2.3" fill="var(--red)"/><circle cx="22" cy="6.5" r="2.3" fill="var(--red)"/>
      <circle cx="8" cy="23.5" r="2.3" fill="var(--red)"/><circle cx="22" cy="23.5" r="2.3" fill="var(--red)"/>
      <circle cx="8" cy="15" r="1.3" fill="#fff"/><circle cx="22" cy="15" r="1.3" fill="#fff"/>
    </g>
  </symbol>
</svg>

<header class="site-header">
  <div class="brand"><span class="brand-mark"></span><span class="brand-name">TIDEWELL-NETWORK</span></div>
  <div class="user-box">
    <div class="avatar" role="img" aria-label="Member profile photo"></div>
    <div class="user-meta">
      <div class="user-line"><span>Dane</span><span>⌄</span><span>|</span>
        <span><svg width="11" height="9" viewBox="0 0 11 9"><ellipse cx="5.5" cy="4" rx="5.5" ry="3.8" fill="#111"/><path d="M1.5 6.5 L0.5 9 L4 7.3Z" fill="#111"/></svg> Comments</span><span>⌄</span></div>
      <div class="user-links">Sign out &nbsp;|&nbsp; Help</div>
    </div>
  </div>
</header>

<nav class="main-nav">
  <ul class="nav-list">
    <li class="active">Forum</li><li>Members</li><li>Calenders</li><li>Blogs</li><li>Files</li><li>Chats (0)</li>
  </ul>
  <div class="search">
    <div class="search-scope"><span>Forum</span><span>⌄</span></div>
    <div class="search-input"><span>Search...</span>
      <svg width="12" height="12" viewBox="0 0 12 12"><circle cx="5" cy="5" r="3.8" fill="none" stroke="#111" stroke-width="1.8"/><path d="M8 8 L11 11" stroke="#111" stroke-width="2"/></svg></div>
  </div>
</nav>

<div class="welcome">
  <div><b>Welcome,</b> User Name, Your Last <span class="hl">Today, &nbsp;Visit 1:21am.</span></div>
  <div class="new-content">View New Content
    <svg width="9" height="9" viewBox="0 0 9 9"><circle cx="1.3" cy="7.7" r="1.3" fill="var(--red)"/><path d="M0 3.5A5.5 5.5 0 0 1 5.5 9M0 0.5A8.5 8.5 0 0 1 8.5 9" fill="none" stroke="var(--red)" stroke-width="1.4"/></svg></div>
</div>

<section class="panel" style="left:31px;top:189px;width:711px;height:350px">
  <div class="panel-head">Important Topics<span class="collapse"></span></div>
  <div class="topic-grid col-head"><span></span><span>Topics</span><span>Started By</span><span>Stats</span><span>Last Post Info</span><span></span></div>
  <div class="rows">
    <div class="topic-grid topic-row"><div class="ico"><svg width="30" height="30"><use href="#board"/></svg></div><div><div class="title">Vestibulum congue et velit euismod..</div><div class="sub">Nullam in bibendum arcu</div></div><div class="started">Rowan 317</div><div class="stats"><div class="title">1Reply</div><div class="sub">95Views</div></div><div class="last"><div class="title">Today 1:31 pm</div><div class="by">By Tessly</div></div><div><span class="check"></span></div></div>
    <div class="topic-grid topic-row"><div class="ico"><svg width="30" height="30"><use href="#board"/></svg></div><div><div class="title">Vestibulum congue et velit euismod..</div><div class="sub">Nullam in bibendum arcu</div></div><div class="started">Rowan 317</div><div class="stats"><div class="title">1Reply</div><div class="sub">95Views</div></div><div class="last"><div class="title">Today 1:31 pm</div><div class="by">By Tessly</div></div><div><span class="check"></span></div></div>
    <div class="topic-grid topic-row"><div class="ico"><svg width="30" height="30"><use href="#board"/></svg></div><div><div class="title">Vestibulum congue et velit euismod..</div><div class="sub">Nullam in bibendum arcu</div></div><div class="started">Rowan 317</div><div class="stats"><div class="title">1Reply</div><div class="sub">95Views</div></div><div class="last"><div class="title">Today 1:31 pm</div><div class="by">By Tessly</div></div><div><span class="check"></span></div></div>
    <div class="topic-grid topic-row"><div class="ico"><svg width="30" height="30"><use href="#board"/></svg></div><div><div class="title">Vestibulum congue et velit euismod..</div><div class="sub">Nullam in bibendum arcu</div></div><div class="started">Rowan 317</div><div class="stats"><div class="title">1Reply</div><div class="sub">95Views</div></div><div class="last"><div class="title">Today 1:31 pm</div><div class="by">By Tessly</div></div><div><span class="check"></span></div></div>
    <div class="topic-grid topic-row"><div class="ico"><svg width="30" height="30"><use href="#board"/></svg></div><div><div class="title">Vestibulum congue et velit euismod..</div><div class="sub">Nullam in bibendum arcu</div></div><div class="started">Rowan 317</div><div class="stats"><div class="title">1Reply</div><div class="sub">95Views</div></div><div class="last"><div class="title">Today 1:31 pm</div><div class="by">By Tessly</div></div><div><span class="check"></span></div></div>
  </div>
</section>

<section class="panel" style="left:31px;top:553px;width:711px;height:240px">
  <div class="panel-head">Forum Topics<span class="collapse"></span></div>
  <div class="topic-grid col-head"><span></span><span>Topics</span><span>Started By</span><span>Stats</span><span>Last Post Info</span><span></span></div>
  <div class="rows">
    <div class="topic-grid topic-row"><div class="ico"><svg width="30" height="30"><use href="#board"/></svg></div><div><div class="title">Vestibulum congue et velit euismod..</div><div class="sub">Nullam in bibendum arcu</div></div><div class="started">Rowan 317</div><div class="stats"><div class="title">1Reply</div><div class="sub">95Views</div></div><div class="last"><div class="title">Today 1:31 pm</div><div class="by">By Tessly</div></div><div><span class="check"></span></div></div>
    <div class="topic-grid topic-row"><div class="ico"><svg width="30" height="30"><use href="#board"/></svg></div><div><div class="title">Vestibulum congue et velit euismod..</div><div class="sub">Nullam in bibendum arcu</div></div><div class="started">Rowan 317</div><div class="stats"><div class="title">1Reply</div><div class="sub">95Views</div></div><div class="last"><div class="title">Today 1:31 pm</div><div class="by">By Tessly</div></div><div><span class="check"></span></div></div>
    <div class="topic-grid topic-row"><div class="ico"><svg width="30" height="30"><use href="#board"/></svg></div><div><div class="title">Vestibulum congue et velit euismod..</div><div class="sub">Nullam in bibendum arcu</div></div><div class="started">Rowan 317</div><div class="stats"><div class="title">1Reply</div><div class="sub">95Views</div></div><div class="last"><div class="title">Today 1:31 pm</div><div class="by">By Tessly</div></div><div><span class="check"></span></div></div>
  </div>
</section>

<section class="panel" style="left:31px;top:807px;width:711px;height:303px">
  <div class="panel-head">Board Statistics<span class="collapse"></span></div>
  <div class="stat-label" style="border-top:none">2 user(s) active in last 15 mins</div>
  <div class="stat-item"><div class="ico"><svg width="30" height="30"><use href="#board"/></svg></div><div class="body"><div class="title">Vestibulum congue et velit euismod cursus pellentesque et ac quam..</div><div class="sub" style="font-style:normal"><span class="red">Show Details by:</span> <i>Last Click &nbsp;| &nbsp;Member Name</i></div></div></div>
  <div class="stat-label">2 user(s) active in last 15 mins</div>
  <div class="stat-item"><div class="ico"><svg width="30" height="30"><use href="#board"/></svg></div><div class="body"><div class="title">Vestibulum congue et velit euismod cursus pellentesque et ac quam..</div><div class="sub" style="font-style:normal"><span class="red">Show Details by:</span> <i>Last Click &nbsp;| &nbsp;Member Name</i></div></div></div>
  <div class="stat-label">2 user(s) active in last 15 mins</div>
  <div class="stat-item"><div class="ico"><svg width="30" height="30"><use href="#board"/></svg></div><div class="body"><div class="title">Vestibulum congue et velit euismod cursus pellentesque et ac quam..</div><div class="sub" style="font-style:normal"><span class="red">Show Details by:</span> <i>Last Click &nbsp;| &nbsp;Member Name</i></div></div></div>
</section>

<aside class="panel" style="left:753px;top:189px;width:229px;height:271px">
  <div class="panel-head">Recent Topics<span class="collapse"></span></div>
  <div class="side-item"><div class="thumb" role="img" aria-label="Member avatar photo"></div><div class="side-text">Vestibulum congue et velit euismod..<div class="side-meta">3hrs ago &nbsp;| &nbsp;Comments</div></div></div>
  <div class="side-item"><div class="thumb" role="img" aria-label="Member avatar photo"></div><div class="side-text">Vestibulum congue et velit euismod..<div class="side-meta">3hrs ago &nbsp;| &nbsp;Comments</div></div></div>
  <div class="side-item"><div class="thumb" role="img" aria-label="Member avatar photo"></div><div class="side-text">Vestibulum congue et velit euismod..<div class="side-meta">3hrs ago &nbsp;| &nbsp;Comments</div></div></div>
  <div class="view-all">View All Updates ›</div>
</aside>

<aside class="panel" style="left:753px;top:471px;width:229px;height:251px">
  <div class="panel-head">Recent Added Topics<span class="collapse"></span></div>
  <div class="list-item">Vestibulum congue et velit euismod..<div class="meta">Jun 01, 2018 &nbsp;| &nbsp;05:28am</div></div>
  <div class="list-item">Vestibulum congue et velit euismod..<div class="meta">Jun 01, 2018 &nbsp;| &nbsp;05:28am</div></div>
  <div class="list-item">Vestibulum congue et velit euismod..<div class="meta">Jun 01, 2018 &nbsp;| &nbsp;05:28am</div></div>
  <div class="list-item">Vestibulum congue et velit euismod..<div class="meta">Jun 01, 2018 &nbsp;| &nbsp;05:28am</div></div>
</aside>

<aside class="panel" style="left:753px;top:734px;width:229px;height:231px">
  <div class="panel-head">Watched Content<span class="collapse"></span></div>
  <div class="tabs"><span class="tab-on">Forum</span><span>Topics</span></div>
  <div class="list-item" style="height:48px">Vestibulum congue et velit euismod..<div class="sub">Nullam in bibendum arcu</div></div>
  <div class="list-item" style="height:49px">Vestibulum congue et velit euismod..<div class="sub">Nullam in bibendum arcu</div></div>
  <div class="list-item" style="height:49px">Vestibulum congue et velit euismod..<div class="sub">Nullam in bibendum arcu</div></div>
</aside>

<div class="online">
  <div class="online-top">
    <svg width="24" height="20" viewBox="0 0 24 20"><circle cx="12" cy="5" r="4" fill="#111"/><circle cx="4.5" cy="7" r="3" fill="#111"/><circle cx="19.5" cy="7" r="3" fill="#111"/><path d="M5 20v-5a7 7 0 0 1 14 0v5Z" fill="#111"/><path d="M0 17v-3a4.5 4.5 0 0 1 6-4v7Z M24 17v-3a4.5 4.5 0 0 0-6-4v7Z" fill="#111"/></svg>
    <span>20 user(s) active in<br>past 15 mins</span>
  </div>
  <div class="online-info">1 members, 19 guest, anoymous user<br>Show by: &nbsp;<i class="red" style="font-size:9.5px">Last Click or Member name</i></div>
</div>

<footer class="site-footer">Copyright © 2018, Company Name All Right reserved.</footer>
</body>
</html>
```